Redesign 2016 Digital Marketing Website and Convert to Wordpress

Technology needed to integrate:

- redesign and convert to wordpress
- gravity forms
- malware and hacker defense / honeypot (must be very secure from hackers)
- I want gravity forms to be a flow that asks many questions with icons and progress bar.
- 1 home page design
- 1 blog design
- 1 design for internal page content
- 1 multi step gravity form
I want to focus on SMB's. We are a marketing agency thats been around since 2016.

Site is: tallpine.agency

I am looking to redesign the homepage, blog page and services page. The services page will be a template for all inner pages of the site. All content needs to be moved into the new design.

I want to get ride of the weird video.

I need you to install gravity forms pro model so we can pass utms.

I need the gravity form to be a multi step form with icons.

All "contact us" or "get a free assesments" call to actions will go to this form only.

step 1:
what is your website

step 2:
what industry are you in
- option
- Home Services
- Legal
- Ecommerce
- Lead Gen

No matter which one they select its going to produce a differnt calculator for them.

Law:
How many leads did you get last month
how much is each ase worth on average
How much revenue do you want to make

Home servicse:
How many bookings did you get last month
How much is each service worht on average
How much revenue do you wangt to make

Ecommerce:
What is your average order value
How muny purchases did you have last month
How much revenue did you drive
How much revenue do you want to drive

For lead gen:
How many leads did you get lawt month
How much revenue did they generate

Step 3:
What is your current advertising budget

step 4:
Do you have a CRM and if so what is it

Step 5:
What is your personal informagtion
name
email
phone

Let me know if this is enough to get you going

Small and medium sized law firms, ecommerce, home services and lead gen customers.

We are a digital marketing agency

• Use whats on the current site and improve upon it

• Must be very secure, developed into a wordpress website. using gravity forms. remove my photo and my staffs photo, depersonalize it so it doesnt mention me or sam crolley. Use the same color scheme. I am looking to redesign the homepage, blog page and services page. The services page will be a template for all inner pages of the site. All content needs to be moved into the new design. I want to get ride of the weird video. I need you to install gravity forms pro model so we can pass utms. I need the gravity form to be a multi step form with icons. All "contact us" or "get a free assesments" call to actions will go to this form only. step 1: what is your website step 2: what industry are you in - option - Home Services - Legal - Ecommerce - Lead Gen No matter which one they select its going to produce a differnt calculator for them. Law: How many leads did you get last month how much is each ase worth on average How much revenue do you want to make Home servicse: How many bookings did you get last month How much is each service worht on average How much revenue do you wangt to make Ecommerce: What is your average order value How muny purchases did you have last month How much revenue did you drive How much revenue do you want to drive For lead gen: How many leads did you get lawt month How much revenue did they generate How much revenue do you want to make Step 3: What is your current advertising budget step 4: Do you have a CRM and if so what is it Step 5: What is your personal informagtion name email phone Let me know if this is enough to get you going
• SHOULD NOT BE SLOPPY, I AM LOOKING FOR ATTENTION TO DETAIL.

```html
<!DOCTYPE html>
<html lang="en">
<head>
<meta charset="utf-8">
<title>Tall Pine – Free Consultation Flow</title>
<link href="https://fonts.googleapis.com/css2?family=Montserrat:wght@400;500;700&family=Roboto:wght@400;500;700&display=swap" rel="stylesheet">
<style>
:root{
  --canvas:#a9a9a9;
  --wine:#7b1c26;
  --wine-deep:#5e131c;
  --ink:#1e1e1e;
  --nav:#232323;
  --footer:#1f1f1f;
  --field:#f3f3f3;
  --field-line:#dedede;
  --muted:#8a8a8a;
  --white:#fff;
}
*{box-sizing:border-box;margin:0;padding:0}
html,body{width:1200px;height:996px;overflow:hidden}
body{background:var(--canvas);font-family:'Roboto',Arial,sans-serif;color:var(--ink);position:relative}
.icons{position:absolute;width:0;height:0}

.page{position:absolute;width:360px;background:var(--white);overflow:hidden}
.page--1{left:35px;top:42px;height:400px}
.page--2{left:420px;top:42px;height:400px}
.page--3{left:805px;top:42px;height:467px}
.page--4{left:35px;top:545px;height:409px}
.page--5{left:420px;top:545px;height:409px}
.page--6{left:805px;top:545px;height:409px}

/* header */
.topbar{position:relative;height:22px;background:var(--white)}
.brand{position:absolute;left:43px;top:4px;display:flex;align-items:center;gap:3px}
.brand__mark{width:14px;height:14px;border-radius:50%;border:1.5px solid var(--wine)}
.brand__name{font-family:'Montserrat',sans-serif;font-size:5.6px;letter-spacing:.4px;color:#555;line-height:1}
.brand__tag{display:block;font-size:2.2px;letter-spacing:.8px;color:#888;margin-top:1.5px}
.callout{position:absolute;left:181px;top:9px;font-size:3.6px;font-weight:700;line-height:1}
.callout__phone{color:var(--wine);font-size:4.4px;font-weight:500;margin-left:3px}
.cta{position:absolute;left:258px;top:5px;width:58px;height:12px;border-radius:6px;background:var(--wine);color:var(--white);font-size:3.6px;font-weight:500;display:flex;align-items:center;justify-content:center}

.nav{height:13px;background:var(--nav);display:flex;align-items:center;padding-left:47px;gap:12.6px}
.nav a{color:var(--white);font-size:3.7px;font-weight:700;text-decoration:none;letter-spacing:.1px}

/* hero */
.hero{position:relative;height:106px;background:radial-gradient(ellipse at 30% 35%,#8a2430 0%,var(--wine) 45%,var(--wine-deep) 100%);overflow:hidden}
.hero__title{position:absolute;left:43px;top:35px;font-family:'Montserrat',sans-serif;font-size:12px;color:var(--white);line-height:1;letter-spacing:.2px}
.hero__title b{font-weight:700}
.hero__title span{font-weight:400}
.hero__text{position:absolute;left:43px;top:54px;width:150px;font-size:4.3px;font-weight:700;color:var(--white);line-height:9px}
.hero__ring{position:absolute;left:250px;top:30px;width:68px;height:68px;border-radius:50%;background:var(--ink);border:2px solid var(--white)}
.hero__photo{position:absolute;left:210px;top:9px;width:96px;height:97px;border-radius:40px 40px 0 0;background:linear-gradient(160deg,#d9e2ec 0%,#a9b8c8 55%,#7d8a98 100%)}

/* content */
.consult{position:relative;background:var(--white)}
.page--1 .consult{height:166px}
.page--2 .consult{height:166px}
.page--3 .consult{height:229px}
.page--4 .consult,.page--5 .consult{height:172px}
.page--6 .consult{height:199px}
.consult__title{position:absolute;left:0;right:0;top:21px;text-align:center;font-family:'Montserrat',sans-serif;font-size:9.8px;font-weight:400;letter-spacing:.2px;line-height:1}
.consult__title b{font-weight:700}
.consult__rule{position:absolute;left:171px;top:35px;width:18px;height:1.2px;background:var(--wine)}

.stepper{position:absolute;left:54px;top:51px;width:252px;display:flex;align-items:center}
.step{width:16px;height:16px;flex:none;border-radius:50%;border:.8px solid var(--wine);color:var(--wine);background:var(--white);display:flex;align-items:center;justify-content:center}
.step svg{width:9px;height:9px}
.step--done{background:var(--wine);color:var(--white);box-shadow:0 0 0 1px #e8c9cd}
.step__label{margin-left:4px;flex:none;line-height:1}
.step__count{display:block;font-size:2.6px;color:var(--muted);margin-bottom:1.2px}
.step__name{font-size:4px;color:var(--ink)}
.link{width:30px;flex:none;border-top:.6px dashed var(--wine);margin:0}
.link--grow{flex:1;margin:0 8px 0 14px;width:auto}

.form-title{position:absolute;left:0;right:0;top:81px;text-align:center;font-size:5.8px;font-weight:700;line-height:1}
.field{position:absolute}
.field__label{display:block;font-size:3.6px;color:var(--ink);margin-bottom:2.5px;line-height:1}
.field__input{height:12px;background:var(--field);border:.5px solid var(--field-line);border-radius:1.5px;font-size:3.2px;color:var(--muted);display:flex;align-items:center;padding-left:6px}

.btn{position:absolute;width:36px;height:13px;border-radius:6.5px;color:var(--white);font-size:3.9px;font-weight:700;display:flex;align-items:center;justify-content:center;gap:2px;letter-spacing:.2px}
.btn--next{right:56px;background:var(--wine)}
.btn--back{left:55px;background:var(--ink)}

.industries{position:absolute;left:56px;top:94px;width:248px;display:flex;gap:5px}
.industry{position:relative;flex:1;height:19px;background:#f5f5f5;border:.5px solid #e6e6e6;display:flex;align-items:center;justify-content:center;gap:4px;font-size:3.9px;font-weight:500}
.industry svg{width:10px;height:10px;color:#555}
.industry--chosen{background:var(--wine);border-color:var(--wine);color:var(--white)}
.industry--chosen svg{color:var(--white)}
.industry--chosen::after{content:"";position:absolute;left:50%;bottom:-3px;margin-left:-2.5px;border-left:2.5px solid transparent;border-right:2.5px solid transparent;border-top:3px solid var(--wine)}

/* footer */
.footer{position:relative;height:96px;background:var(--footer);color:var(--white)}
.footer__brand{position:absolute;left:42px;top:24px;display:flex;align-items:center;gap:4px}
.footer__mark{width:17px;height:17px;border-radius:50%;border:1.6px solid var(--wine)}
.footer__name{font-family:'Montserrat',sans-serif;font-size:7.6px;letter-spacing:.6px;line-height:1}
.footer__tag{display:block;font-size:2.4px;letter-spacing:1.4px;margin-top:2.5px;color:#ccc}
.social{position:absolute;left:59px;top:50px;display:flex;gap:4.5px}
.social span{width:10px;height:10px;border-radius:50%;border:.6px solid var(--white)}
.divider{position:absolute;top:16px;height:58px;width:.5px;background:#444}
.divider--a{left:137px}
.divider--b{left:218px}
.footer__head{position:absolute;top:17px;font-size:4.1px;font-weight:700;letter-spacing:.2px;line-height:1}
.quick{left:162px}
.info{left:243px}
.links{position:absolute;left:162px;top:29px;list-style:none}
.links li{font-size:3.6px;line-height:6.3px;color:#ddd}
.contact{position:absolute;left:243px;top:28px;list-style:none;width:80px}
.contact li{position:relative;padding-left:9px;font-size:3.9px;font-weight:500;line-height:7px;margin-bottom:2px}
.contact svg{position:absolute;left:0;top:1.5px;width:4.5px;height:4.5px;color:var(--wine)}
.contact .tel{text-decoration:underline}
.footer__bottom{position:absolute;left:43px;right:43px;top:72px;border-top:.5px solid #3a3a3a;padding-top:7px;display:flex;justify-content:space-between;font-size:3.5px;color:#ddd}
.legal span{margin-left:4px}
</style>
</head>
<body>

<svg class="icons" aria-hidden="true">
  <symbol id="i-web" viewBox="0 0 24 24"><g fill="none" stroke="currentColor" stroke-width="1.6"><circle cx="12" cy="12" r="9"/><ellipse cx="12" cy="12" rx="4" ry="9"/><path d="M3 12h18M5 7h14M5 17h14"/></g></symbol>
  <symbol id="i-ind" viewBox="0 0 24 24"><g fill="none" stroke="currentColor" stroke-width="1.6"><circle cx="8" cy="8" r="3.5"/><circle cx="16" cy="8" r="3.5"/><circle cx="8" cy="16" r="3.5"/><circle cx="16" cy="16" r="3.5"/></g></symbol>
  <symbol id="i-budget" viewBox="0 0 24 24"><g fill="none" stroke="currentColor" stroke-width="1.6"><rect x="4" y="4" width="12" height="16" rx="1"/><circle cx="15" cy="14" r="5"/><path d="M16.5 12.3c-.6-.6-3-.7-3 .6s3 .7 3 2.1-2.4 1.2-3 .6M15 10.8v6.4"/></g></symbol>
  <symbol id="i-crm" viewBox="0 0 24 24"><g fill="none" stroke="currentColor" stroke-width="1.6"><rect x="4" y="3" width="16" height="18" rx="1"/><path d="M8 8h8M8 12h8M8 16h5"/></g></symbol>
  <symbol id="i-user" viewBox="0 0 24 24"><g fill="none" stroke="currentColor" stroke-width="1.6"><circle cx="12" cy="8.5" r="4"/><path d="M4.5 20c1-4 4-5.5 7.5-5.5s6.5 1.5 7.5 5.5"/></g></symbol>
  <symbol id="i-law" viewBox="0 0 24 24"><g fill="none" stroke="currentColor" stroke-width="1.4"><path d="M3 9l9-5 9 5zM4 20h16M3 22h18M6 10v9M10 10v9M14 10v9M18 10v9"/></g></symbol>
  <symbol id="i-home" viewBox="0 0 24 24"><g fill="none" stroke="currentColor" stroke-width="1.4"><rect x="3" y="3" width="18" height="18"/><path d="M6 12l6-5 6 5M8 11v7h8v-7M10 18v-4h4v4"/></g></symbol>
  <symbol id="i-cart" viewBox="0 0 24 24"><g fill="none" stroke="currentColor" stroke-width="1.4"><rect x="3" y="3" width="18" height="13"/><path d="M7 7h2l1.5 5h5.5l1-4h-7.5M9 20h6M12 16v4"/></g></symbol>
  <symbol id="i-lead" viewBox="0 0 24 24"><g fill="none" stroke="currentColor" stroke-width="1.4"><circle cx="12" cy="5" r="2.5"/><circle cx="6" cy="10" r="2.5"/><circle cx="18" cy="10" r="2.5"/><path d="M9 11h6M12 8v5M8 22v-5a4 4 0 018 0v5M2 18a4 4 0 017 0M15 18a4 4 0 017 0"/></g></symbol>
  <symbol id="i-pin" viewBox="0 0 24 24"><path fill="currentColor" d="M12 2a7 7 0 00-7 7c0 5 7 13 7 13s7-8 7-13a7 7 0 00-7-7zm0 9.5A2.5 2.5 0 1112 6.5a2.5 2.5 0 010 5z"/></symbol>
  <symbol id="i-mail" viewBox="0 0 24 24"><path fill="currentColor" d="M2 5h20v14H2zm2 2v.5l8 5 8-5V7z"/></symbol>
  <symbol id="i-phone" viewBox="0 0 24 24"><path fill="currentColor" d="M6.6 10.8a15 15 0 006.6 6.6l2.2-2.2a1 1 0 011-.2 11.4 11.4 0 003.6.6 1 1 0 011 1V20a1 1 0 01-1 1A17 17 0 013 4a1 1 0 011-1h3.5a1 1 0 011 1c0 1.2.2 2.5.6 3.6a1 1 0 01-.3 1z"/></symbol>
</svg>

<!-- Page 1 -->
<section class="page page--1">
  <header class="topbar">
    <div class="brand"><span class="brand__mark"></span><span class="brand__name">TALL PINE<span class="brand__tag">GROWTH MARKETING</span></span></div>
    <div class="callout">OR CALL US NOW:<span class="callout__phone">(480) 555-0142</span></div>
    <div class="cta">Get a Free Consultation</div>
  </header>
  <nav class="nav"><a>HOME</a><a>ABOUT US</a><a>OUR INDUSTRIES</a><a>OUR SERVICES</a><a>RESOURCES</a><a>TRAINING</a><a>BLOG</a><a>CONTACT US</a></nav>
  <div class="hero">
    <h1 class="hero__title"><b>GROW YOUR</b> <span>REVENUE</span></h1>
    <p class="hero__text">Are you ready to kick your business into high gear? Our strategists are standing by. Contact us now!</p>
    <div class="hero__ring"></div>
    <div class="hero__photo" role="img" aria-label="Smiling businessman in a light blue shirt holding a laptop"></div>
  </div>
  <div class="consult">
    <h2 class="consult__title">GET A FREE <b>CONSULTATION</b></h2><div class="consult__rule"></div>
    <div class="stepper">
      <span class="step step--done"><svg><use href="#i-web"/></svg></span>
      <span class="step__label"><span class="step__count">Step1/5</span><span class="step__name">Website Information</span></span>
      <span class="link link--grow"></span>
      <span class="step"><svg><use href="#i-ind"/></svg></span><span class="link"></span>
      <span class="step"><svg><use href="#i-budget"/></svg></span><span class="link"></span>
      <span class="step"><svg><use href="#i-crm"/></svg></span><span class="link"></span>
      <span class="step"><svg><use href="#i-user"/></svg></span>
    </div>
    <h3 class="form-title">Website Information</h3>
    <div class="field" style="left:57px;top:97px;width:247px"><span class="field__label">What is Your Website</span><div class="field__input">Enter Your Website</div></div>
    <div class="btn btn--next" style="top:129px">NEXT →</div>
  </div>
  <footer class="footer">
    <div class="footer__brand"><span class="footer__mark"></span><span class="footer__name">TALL PINE<span class="footer__tag">GROWTH MARKETING</span></span></div>
    <div class="social"><span></span><span></span><span></span></div>
    <span class="divider divider--a"></span><span class="divider divider--b"></span>
    <h4 class="footer__head quick">QUICK LINKS</h4>
    <ul class="links"><li>About Us</li><li>Our Industries</li><li>Our Services</li><li>Resources</li><li>Training</li><li>Blog</li></ul>
    <h4 class="footer__head info">CONTACT INFO</h4>
    <ul class="contact">
      <li><svg><use href="#i-pin"/></svg>Address: 18 W. Juniper Ave, Suite 310, Mesa, 85201</li>
      <li><svg><use href="#i-mail"/></svg>sales@tallpine.agency</li>
      <li><svg><use href="#i-phone"/></svg><span class="tel">(480) 555-0142</span></li>
    </ul>
    <div class="footer__bottom"><span>© 2024 Tall Pine. All Rights Reserved.</span><span class="legal">Privacy <span>|</span><span>Terms</span> <span>|</span><span>Disclaimer</span></span></div>
  </footer>
</section>

<!-- Page 2 -->
<section class="page page--2">
  <header class="topbar">
    <div class="brand"><span class="brand__mark"></span><span class="brand__name">TALL PINE<span class="brand__tag">GROWTH MARKETING</span></span></div>
    <div class="callout">OR CALL US NOW:<span class="callout__phone">(480) 555-0142</span></div>
    <div class="cta">Get a Free Consultation</div>
  </header>
  <nav class="nav"><a>HOME</a><a>ABOUT US</a><a>OUR INDUSTRIES</a><a>OUR SERVICES</a><a>RESOURCES</a><a>TRAINING</a><a>BLOG</a><a>CONTACT US</a></nav>
  <div class="hero">
    <h1 class="hero__title"><b>GROW YOUR</b> <span>REVENUE</span></h1>
    <p class="hero__text">Are you ready to kick your business into high gear? Our strategists are standing by. Contact us now!</p>
    <div class="hero__ring"></div>
    <div class="hero__photo" role="img" aria-label="Smiling businessman in a light blue shirt holding a laptop"></div>
  </div>
  <div class="consult">
    <h2 class="consult__title">GET A FREE <b>CONSULTATION</b></h2><div class="consult__rule"></div>
    <div class="stepper">
      <span class="step step--done"><svg><use href="#i-web"/></svg></span><span class="link"></span>
      <span class="step step--done"><svg><use href="#i-ind"/></svg></span>
      <span class="step__label"><span class="step__count">Step 2/5</span><span class="step__name">Industry Information</span></span>
      <span class="link link--grow"></span>
      <span class="step"><svg><use href="#i-budget"/></svg></span><span class="link"></span>
      <span class="step"><svg><use href="#i-crm"/></svg></span><span class="link"></span>
      <span class="step"><svg><use href="#i-user"/></svg></span>
    </div>
    <h3 class="form-title">What Industry are you in</h3>
    <div class="industries">
      <div class="industry"><svg><use href="#i-law"/></svg>Law</div>
      <div class="industry"><svg><use href="#i-home"/></svg>Home services</div>
      <div class="industry"><svg><use href="#i-cart"/></svg>Ecommerce</div>
      <div class="industry"><svg><use href="#i-lead"/></svg>Lead Gen</div>
    </div>
    <div class="btn btn--back" style="top:125px">← BACK</div>
    <div class="btn btn--next" style="top:125px">NEXT →</div>
  </div>
  <footer class="footer">
    <div class="footer__brand"><span class="footer__mark"></span><span class="footer__name">TALL PINE<span class="footer__tag">GROWTH MARKETING</span></span></div>
    <div class="social"><span></span><span></span><span></span></div>
    <span class="divider divider--a"></span><span class="divider divider--b"></span>
    <h4 class="footer__head quick">QUICK LINKS</h4>
    <ul class="links"><li>About Us</li><li>Our Industries</li><li>Our Services</li><li>Resources</li><li>Training</li><li>Blog</li></ul>
    <h4 class="footer__head info">CONTACT INFO</h4>
    <ul class="contact">
      <li><svg><use href="#i-pin"/></svg>Address: 18 W. Juniper Ave, Suite 310, Mesa, 85201</li>
      <li><svg><use href="#i-mail"/></svg>sales@tallpine.agency</li>
      <li><svg><use href="#i-phone"/></svg><span class="tel">(480) 555-0142</span></li>
    </ul>
    <div class="footer__bottom"><span>© 2024 Tall Pine. All Rights Reserved.</span><span class="legal">Privacy <span>|</span><span>Terms</span> <span>|</span><span>Disclaimer</span></span></div>
  </footer>
</section>

<!-- Page 3 -->
<section class="page page--3">
  <header class="topbar">
    <div class="brand"><span class="brand__mark"></span><span class="brand__name">TALL PINE<span class="brand__tag">GROWTH MARKETING</span></span></div>
    <div class="callout">OR CALL US NOW:<span class="callout__phone">(480) 555-0142</span></div>
    <div class="cta">Get a Free Consultation</div>
  </header>
  <nav class="nav"><a>HOME</a><a>ABOUT US</a><a>OUR INDUSTRIES</a><a>OUR SERVICES</a><a>RESOURCES</a><a>TRAINING</a><a>BLOG</a><a>CONTACT US</a></nav>
  <div class="hero">
    <h1 class="hero__title"><b>GROW YOUR</b> <span>REVENUE</span></h1>
    <p class="hero__text">Are you ready to kick your business into high gear? Our strategists are standing by. Contact us now!</p>
    <div class="hero__ring"></div>
    <div class="hero__photo" role="img" aria-label="Smiling businessman in a light blue shirt holding a laptop"></div>
  </div>
  <div class="consult">
    <h2 class="consult__title">GET A FREE <b>CONSULTATION</b></h2><div class="consult__rule"></div>
    <div class="stepper">
      <span class="step step--done"><svg><use href="#i-web"/></svg></span><span class="link"></span>
      <span class="step step--done"><svg><use href="#i-ind"/></svg></span>
      <span class="step__label"><span class="step__count">Step 2/5</span><span class="step__name">Industry Information</span></span>
      <span class="link link--grow"></span>
      <span class="step"><svg><use href="#i-budget"/></svg></span><span class="link"></span>
      <span class="step"><svg><use href="#i-crm"/></svg></span><span class="link"></span>
      <span class="step"><svg><use href="#i-user"/></svg></span>
    </div>
    <h3 class="form-title">What Industry are you in</h3>
    <div class="industries">
      <div class="industry industry--chosen"><svg><use href="#i-law"/></svg>Law</div>
      <div class="industry"><svg><use href="#i-home"/></svg>Home services</div>
      <div class="industry"><svg><use href="#i-cart"/></svg>Ecommerce</div>
      <div class="industry"><svg><use href="#i-lead"/></svg>Lead Gen</div>
    </div>
    <div class="field" style="left:57px;top:129px;width:120px"><span class="field__label">How many leads did you get last month</span><div class="field__input">Enter Leads</div></div>
    <div class="field" style="left:183px;top:129px;width:120px"><span class="field__label">How much is each ase worth on average</span><div class="field__input">Enter Average</div></div>
    <div class="field" style="left:57px;top:160px;width:120px"><span class="field__label">How much revenue do you want to make</span><div class="field__input">Enter Revenue</div></div>
    <div class="btn btn--back" style="top:195px">← BACK</div>
    <div class="btn btn--next" style="top:195px">NEXT →</div>
  </div>
  <footer class="footer">
    <div class="footer__brand"><span class="footer__mark"></span><span class="footer__name">TALL PINE<span class="footer__tag">GROWTH MARKETING</span></span></div>
    <div class="social"><span></span><span></span><span></span></div>
    <span class="divider divider--a"></span><span class="divider divider--b"></span>
    <h4 class="footer__head quick">QUICK LINKS</h4>
    <ul class="links"><li>About Us</li><li>Our Industries</li><li>Our Services</li><li>Resources</li><li>Training</li><li>Blog</li></ul>
    <h4 class="footer__head info">CONTACT INFO</h4>
    <ul class="contact">
      <li><svg><use href="#i-pin"/></svg>Address: 18 W. Juniper Ave, Suite 310, Mesa, 85201</li>
      <li><svg><use href="#i-mail"/></svg>sales@tallpine.agency</li>
      <li><svg><use href="#i-phone"/></svg><span class="tel">(480) 555-0142</span></li>
    </ul>
    <div class="footer__bottom"><span>© 2024 Tall Pine. All Rights Reserved.</span><span class="legal">Privacy <span>|</span><span>Terms</span> <span>|</span><span>Disclaimer</span></span></div>
  </footer>
</section>

<!-- Page 4 -->
<section class="page page--4">
  <header class="topbar">
    <div class="brand"><span class="brand__mark"></span><span class="brand__name">TALL PINE<span class="brand__tag">GROWTH MARKETING</span></span></div>
    <div class="callout">OR CALL US NOW:<span class="callout__phone">(480) 555-0142</span></div>
    <div class="cta">Get a Free Consultation</div>
  </header>
  <nav class="nav"><a>HOME</a><a>ABOUT US</a><a>OUR INDUSTRIES</a><a>OUR SERVICES</a><a>RESOURCES</a><a>TRAINING</a><a>BLOG</a><a>CONTACT US</a></nav>
  <div class="hero">
    <h1 class="hero__title"><b>GROW YOUR</b> <span>REVENUE</span></h1>
    <p class="hero__text">Are you ready to kick your business into high gear? Our strategists are standing by. Contact us now!</p>
    <div class="hero__ring"></div>
    <div class="hero__photo" role="img" aria-label="Smiling businessman in a light blue shirt holding a laptop"></div>
  </div>
  <div class="consult">
    <h2 class="consult__title">GET A FREE <b>CONSULTATION</b></h2><div class="consult__rule"></div>
    <div class="stepper">
      <span class="step step--done"><svg><use href="#i-web"/></svg></span><span class="link"></span>
      <span class="step step--done"><svg><use href="#i-ind"/></svg></span><span class="link"></span>
      <span class="step step--done"><svg><use href="#i-budget"/></svg></span>
      <span class="step__label"><span class="step__count">Step 3/5</span><span class="step__name">Budget Information</span></span>
      <span class="link link--grow"></span>
      <span class="step"><svg><use href="#i-crm"/></svg></span><span class="link"></span>
      <span class="step"><svg><use href="#i-user"/></svg></span>
    </div>
    <h3 class="form-title">Budget Information</h3>
    <div class="field" style="left:57px;top:97px;width:247px"><span class="field__label">What is your current advertising budget</span><div class="field__input">Enter Advertising Budget</div></div>
    <div class="btn btn--back" style="top:134px">← BACK</div>
    <div class="btn btn--next" style="top:134px">NEXT →</div>
  </div>
  <footer class="footer">
    <div class="footer__brand"><span class="footer__mark"></span><span class="footer__name">TALL PINE<span class="footer__tag">GROWTH MARKETING</span></span></div>
    <div class="social"><span></span><span></span><span></span></div>
    <span class="divider divider--a"></span><span class="divider divider--b"></span>
    <h4 class="footer__head quick">QUICK LINKS</h4>
    <ul class="links"><li>About Us</li><li>Our Industries</li><li>Our Services</li><li>Resources</li><li>Training</li><li>Blog</li></ul>
    <h4 class="footer__head info">CONTACT INFO</h4>
    <ul class="contact">
      <li><svg><use href="#i-pin"/></svg>Address: 18 W. Juniper Ave, Suite 310, Mesa, 85201</li>
      <li><svg><use href="#i-mail"/></svg>sales@tallpine.agency</li>
      <li><svg><use href="#i-phone"/></svg><span class="tel">(480) 555-0142</span></li>
    </ul>
    <div class="footer__bottom"><span>© 2024 Tall Pine. All Rights Reserved.</span><span class="legal">Privacy <span>|</span><span>Terms</span> <span>|</span><span>Disclaimer</span></span></div>
  </footer>
</section>

<!-- Page 5 -->
<section class="page page--5">
  <header class="topbar">
    <div class="brand"><span class="brand__mark"></span><span class="brand__name">TALL PINE<span class="brand__tag">GROWTH MARKETING</span></span></div>
    <div class="callout">OR CALL US NOW:<span class="callout__phone">(480) 555-0142</span></div>
    <div class="cta">Get a Free Consultation</div>
  </header>
  <nav class="nav"><a>HOME</a><a>ABOUT US</a><a>OUR INDUSTRIES</a><a>OUR SERVICES</a><a>RESOURCES</a><a>TRAINING</a><a>BLOG</a><a>CONTACT US</a></nav>
  <div class="hero">
    <h1 class="hero__title"><b>GROW YOUR</b> <span>REVENUE</span></h1>
    <p class="hero__text">Are you ready to kick your business into high gear? Our strategists are standing by. Contact us now!</p>
    <div class="hero__ring"></div>
    <div class="hero__photo" role="img" aria-label="Smiling businessman in a light blue shirt holding a laptop"></div>
  </div>
  <div class="consult">
    <h2 class="consult__title">GET A FREE <b>CONSULTATION</b></h2><div class="consult__rule"></div>
    <div class="stepper">
      <span class="step step--done"><svg><use href="#i-web"/></svg></span><span class="link"></span>
      <span class="step step--done"><svg><use href="#i-ind"/></svg></span><span class="link"></span>
      <span class="step step--done"><svg><use href="#i-budget"/></svg></span><span class="link"></span>
      <span class="step step--done"><svg><use href="#i-crm"/></svg></span>
      <span class="step__label"><span class="step__count">Step 4/5</span><span class="step__name">CRM Information</span></span>
      <span class="link link--grow"></span>
      <span class="step"><svg><use href="#i-user"/></svg></span>
    </div>
    <h3 class="form-title">CRM Information</h3>
    <div class="field" style="left:57px;top:97px;width:247px"><span class="field__label">Do you have a CRM and if so what is it</span><div class="field__input">Enter CRM</div></div>
    <div class="btn btn--back" style="top:134px">← BACK</div>
    <div class="btn btn--next" style="top:134px">NEXT →</div>
  </div>
  <footer class="footer">
    <div class="footer__brand"><span class="footer__mark"></span><span class="footer__name">TALL PINE<span class="footer__tag">GROWTH MARKETING</span></span></div>
    <div class="social"><span></span><span></span><span></span></div>
    <span class="divider divider--a"></span><span class="divider divider--b"></span>
    <h4 class="footer__head quick">QUICK LINKS</h4>
    <ul class="links"><li>About Us</li><li>Our Industries</li><li>Our Services</li><li>Resources</li><li>Training</li><li>Blog</li></ul>
    <h4 class="footer__head info">CONTACT INFO</h4>
    <ul class="contact">
      <li><svg><use href="#i-pin"/></svg>Address: 18 W. Juniper Ave, Suite 310, Mesa, 85201</li>
      <li><svg><use href="#i-mail"/></svg>sales@tallpine.agency</li>
      <li><svg><use href="#i-phone"/></svg><span class="tel">(480) 555-0142</span></li>
    </ul>
    <div class="footer__bottom"><span>© 2024 Tall Pine. All Rights Reserved.</span><span class="legal">Privacy <span>|</span><span>Terms</span> <span>|</span><span>Disclaimer</span></span></div>
  </footer>
</section>

<!-- Page 6 -->
<section class="page page--6">
  <header class="topbar">
    <div class="brand"><span class="brand__mark"></span><span class="brand__name">TALL PINE<span class="brand__tag">GROWTH MARKETING</span></span></div>
    <div class="callout">OR CALL US NOW:<span class="callout__phone">(480) 555-0142</span></div>
    <div class="cta">Get a Free Consultation</div>
  </header>
  <nav class="nav"><a>HOME</a><a>ABOUT US</a><a>OUR INDUSTRIES</a><a>OUR SERVICES</a><a>RESOURCES</a><a>TRAINING</a><a>BLOG</a><a>CONTACT US</a></nav>
  <div class="hero">
    <h1 class="hero__title"><b>GROW YOUR</b> <span>REVENUE</span></h1>
    <p class="hero__text">Are you ready to kick your business into high gear? Our strategists are standing by. Contact us now!</p>
    <div class="hero__ring"></div>
    <div class="hero__photo" role="img" aria-label="Smiling businessman in a light blue shirt holding a laptop"></div>
  </div>
  <div class="consult">
    <h2 class="consult__title">GET A FREE <b>CONSULTATION</b></h2><div class="consult__rule"></div>
    <div class="stepper" style="width:auto">
      <span class="step step--done"><svg><use href="#i-web"/></svg></span><span class="link"></span>
      <span class="step step--done"><svg><use href="#i-ind"/></svg></span><span class="link"></span>
      <span class="step step--done"><svg><use href="#i-budget"/></svg></span><span class="link"></span>
      <span class="step step--done"><svg><use href="#i-crm"/></svg></span><span class="link"></span>
      <span class="step step--done"><svg><use href="#i-user"/></svg></span>
      <span class="step__label"><span class="step__count">Step 5/5</span><span class="step__name">Personal Information</span></span>
    </div>
    <h3 class="form-title">Personal Information</h3>
    <div class="field" style="left:57px;top:97px;width:120px"><span class="field__label">Name</span><div class="field__input">Enter Name</div></div>
    <div class="field" style="left:183px;top:97px;width:120px"><span class="field__label">Email</span><div class="field__input">Enter Email Address</div></div>
    <div class="field" style="left:57px;top:127px;width:120px"><span class="field__label">Phone</span><div class="field__input">Enter Phone Number</div></div>
    <div class="btn btn--back" style="top:162px">← BACK</div>
    <div class="btn btn--next" style="top:162px">SUBMIT →</div>
  </div>
  <footer class="footer">
    <div class="footer__brand"><span class="footer__mark"></span><span class="footer__name">TALL PINE<span class="footer__tag">GROWTH MARKETING</span></span></div>
    <div class="social"><span></span><span></span><span></span></div>
    <span class="divider divider--a"></span><span class="divider divider--b"></span>
    <h4 class="footer__head quick">QUICK LINKS</h4>
    <ul class="links"><li>About Us</li><li>Our Industries</li><li>Our Services</li><li>Resources</li><li>Training</li><li>Blog</li></ul>
    <h4 class="footer__head info">CONTACT INFO</h4>
    <ul class="contact">
      <li><svg><use href="#i-pin"/></svg>Address: 18 W. Juniper Ave, Suite 310, Mesa, 85201</li>
      <li><svg><use href="#i-mail"/></svg>sales@tallpine.agency</li>
      <li><svg><use href="#i-phone"/></svg><span class="tel">(480) 555-0142</span></li>
    </ul>
  </footer>
</section>

</body>
</html>
```